Local fast-growing company in the service sector

We are looking for a modern business card design, which should also appear on our letterheads

Target Market(s)

Private and industrial sectors

Contact Information for Business Card

Vorname Name
Kellberger Str. 18
74523 Hallbach
Tel.: 07146-839214-0
Name@agentur-kvtl.de

Colors
9d9d9d
919191
aaaaaa

Requirements
Must have
• The logo (file) in silver

```html
<!DOCTYPE html>
<html lang="de">
<head>
<meta charset="utf-8">
<title>KVTL Visitenkarte</title>
<link rel="stylesheet" href="https://fonts.googleapis.com/css2?family=Roboto:wght@400;500;700;900&display=swap">
<style>
  :root {
    --silver-dark: #919191;
    --silver-mid: #9d9d9d;
    --silver-light: #aaaaaa;
    --band: #a9a9aa;
    --card: #ffffff;
    --stage: #3a3a3a;
    --text-dark: #4a4a4a;
    --text-light: #ffffff;
  }
  * { box-sizing: border-box; margin: 0; padding: 0; }
  html, body { width: 1200px; height: 900px; overflow: hidden; }
  body {
    background: var(--stage);
    font-family: "Roboto", Arial, sans-serif;
    position: relative;
  }
  .card {
    position: absolute;
    left: 302px;
    width: 596px;
    height: 340px;
    background: var(--card);
    border-radius: 18px;
    overflow: hidden;
  }
  .card--back { top: 85px; }
  .card--front { top: 475px; }

  .wordmark {
    position: absolute;
    display: flex;
    align-items: center;
    gap: 14px;
    font-weight: 900;
    font-size: 78px;
    letter-spacing: 2px;
    color: var(--silver-mid);
    line-height: 1;
    white-space: nowrap;
  }
  .wordmark__square {
    width: 58px;
    height: 58px;
    background: var(--silver-light);
  }
  .card--back .wordmark { left: 175px; top: 128px; }
  .card--front .wordmark { left: 175px; top: 56px; }

  .contact-band {
    position: absolute;
    left: 0; right: 0;
    top: 196px;
    height: 80px;
    background: linear-gradient(90deg, #c4c4c4 0%, var(--band) 6%, var(--band) 100%);
    color: var(--text-light);
    display: flex;
    align-items: center;
  }
  .contact-band__name {
    width: 285px;
    text-align: right;
    padding-right: 26px;
    font-size: 22px;
    font-weight: 500;
    white-space: nowrap;
  }
  .contact-band__divider {
    width: 1px;
    height: 46px;
    background: var(--text-light);
  }
  .contact-band__list {
    list-style: none;
    padding-left: 22px;
    font-size: 18px;
    font-weight: 500;
  }
  .contact-band__list li {
    display: flex;
    align-items: center;
    gap: 10px;
    line-height: 26px;
    white-space: nowrap;
  }
  .contact-band__list svg { width: 16px; height: 16px; flex: none; }

  .address-strip {
    position: absolute;
    left: 0; right: 0;
    top: 276px;
    height: 64px;
    background: linear-gradient(180deg, #e6e6e6 0%, #f7f7f7 45%, #dcdcdc 100%);
    display: flex;
    align-items: center;
    padding-left: 110px;
    font-size: 16px;
    color: var(--text-dark);
    white-space: nowrap;
  }
</style>
</head>
<body>
  <section class="card card--back" aria-label="Kartenrückseite">
    <div class="wordmark"><span class="wordmark__square"></span>KVTL</div>
  </section>

  <section class="card card--front" aria-label="Kartenvorderseite">
    <div class="wordmark"><span class="wordmark__square"></span>KVTL</div>

    <div class="contact-band">
      <p class="contact-band__name">Vorname Name</p>
      <span class="contact-band__divider"></span>
      <ul class="contact-band__list">
        <li>
          <svg viewBox="0 0 16 16" aria-hidden="true"><rect width="16" height="16" rx="3" fill="#fff"/><path d="M5 3.5l2 2-1 1.2c.6 1.3 1.6 2.3 2.9 2.9l1.2-1 2 2-1.2 1.4C7.6 11.8 4.2 8.4 3.6 5.1z" fill="#a9a9aa"/></svg>
          07146-839214-0
        </li>
        <li>
          <svg viewBox="0 0 16 16" aria-hidden="true"><rect width="16" height="16" rx="3" fill="#fff"/><rect x="3" y="4.5" width="10" height="7" fill="none" stroke="#a9a9aa" stroke-width="1.2"/><path d="M3 4.5l5 4 5-4" fill="none" stroke="#a9a9aa" stroke-width="1.2"/></svg>
          Name@agentur-kvtl.de
        </li>
      </ul>
    </div>

    <div class="address-strip">Kellberger Str. 18, 74523 Hallbach</div>
  </section>
</body>
</html>
```